High-end construction company needs a business card design

We need a modern looking business card that draws people in, is memorable and looks so good people will want to sick it on their fridges.
On the first side what is needed are:
Logo
My name - Tomasz Brelwik
Title - Managing Director
Website - www.varkelt.co.uk
Email - tomasz@varkelt.co.uk
Telephone - 020 5194 6281
Mobile - 07845139072
On the back side was is needed is a list of all the services we provide:
-Kitchen Renovations
-Bathroom Renovations
-House Renovations
-Garage Conversions
-Extensions
-Loft Conversions
-Conservatories
-Carpentry
-Tiling
-Electrical
-Plumbing & Heating
-Bricklaying
-Landscaping
-Decorating
-Plastering
We would like the colours to be the same shades as on the logo with grey or black for the words.
Target Market(s)
Anyone who needs building work done
Contact Information for Business Card
This business card is for a construction company which strives to deliver excellent service and quality.
The look and feel of the card should represent this.
Requirements
Must have
- On the first side what is needed are:
Logo
My name - Tomasz Brelwik
Title - Managing Director
Website - www.varkelt.co.uk
Email - tomasz@varkelt.co.uk
Telephone - 020 5194 6281
Mobile - 07845139072
Nice to have
- Cool looking features

```html
<!DOCTYPE html>
<html lang="en">
<head>
<meta charset="utf-8">
<title>Varkelt Construction – Business Card</title>
<link href="https://fonts.googleapis.com/css2?family=Montserrat:wght@700;800&family=Open+Sans:wght@400;600&display=swap" rel="stylesheet">
<style>
  :root {
    --bg: #141414;
    --card: #2d2d2f;
    --card-edge: #38383a;
    --green: #6cc03c;
    --green-dark: #3f8e3a;
    --text: #f2f2f2;
  }
  * { box-sizing: border-box; margin: 0; padding: 0; }
  html, body { width: 1200px; height: 896px; overflow: hidden; }
  body {
    background: var(--bg);
    font-family: "Open Sans", Arial, sans-serif;
    color: var(--text);
    position: relative;
  }
  .card {
    position: absolute;
    left: 260px;
    width: 680px;
    height: 388px;
    background: linear-gradient(135deg, var(--card-edge), var(--card));
    overflow: hidden;
    box-shadow: 0 12px 30px rgba(0,0,0,.5);
  }
  .card--back { top: 40px; }
  .card--front { top: 468px; }

  .card__band {
    position: absolute; left: 0; right: 0; bottom: 0; height: 16px;
    background: linear-gradient(100deg, var(--green) 0 62%, var(--green-dark) 62% 100%);
  }
  .card__band::after {
    content: ""; position: absolute; left: 0; right: 0; top: 0; height: 5px;
    background: rgba(255,255,255,.12);
  }

  .brand {
    display: flex; align-items: center; gap: 12px;
    font-family: "Montserrat", Arial, sans-serif;
    font-weight: 800;
    color: var(--green);
    letter-spacing: 1px;
    text-transform: uppercase;
  }
  .brand__mark { background: var(--green); flex: none; }

  /* Back: services */
  .card--back .brand {
    position: absolute; left: 0; right: 0; top: 62px;
    justify-content: center; font-size: 40px;
  }
  .card--back .brand__mark { width: 30px; height: 30px; }
  .services__title {
    position: absolute; left: 0; right: 0; top: 160px;
    display: flex; align-items: center; justify-content: center; gap: 16px;
    font-family: "Montserrat", Arial, sans-serif; font-weight: 700;
    color: var(--green); font-size: 22px; letter-spacing: 1px;
  }
  .services__title::before, .services__title::after {
    content: ""; width: 150px; height: 2px; background: var(--green-dark);
  }
  .services__list {
    position: absolute; left: 40px; right: 40px; top: 212px;
    list-style: none; text-align: center;
    font-size: 16.5px; line-height: 32px;
  }
  .services__list li { display: inline; }
  .services__list li::before {
    content: "•"; color: var(--green); margin: 0 6px 0 4px;
  }

  /* Front: contact */
  .card--front .brand {
    position: absolute; right: 44px; top: 52px; font-size: 32px;
  }
  .card--front .brand__mark { width: 24px; height: 24px; }
  .person { position: absolute; left: 48px; top: 150px; }
  .person__name {
    font-family: "Montserrat", Arial, sans-serif; font-weight: 800;
    font-size: 27px; color: var(--green); text-transform: uppercase; letter-spacing: .5px;
  }
  .person__title { font-size: 17px; margin-top: 2px; }
  .divider {
    position: absolute; left: 170px; right: 44px; top: 236px;
    height: 2px; background: var(--green-dark);
  }
  .contact-phone {
    position: absolute; left: 170px; top: 262px;
    list-style: none; font-size: 18px; line-height: 28px;
  }
  .contact-online {
    position: absolute; right: 44px; top: 262px;
    list-style: none; text-align: right; font-size: 16px; line-height: 28px;
  }
  .contact-item { display: flex; align-items: center; gap: 10px; }
  .contact-online .contact-item { justify-content: flex-end; }
  .icon { width: 16px; height: 16px; flex: none; fill: var(--green); }
</style>
</head>
<body>

  <section class="card card--back" aria-label="Card back – services">
    <div class="brand"><span class="brand__mark"></span>Varkelt Construction</div>
    <h2 class="services__title">SERVICES</h2>
    <ul class="services__list">
      <li>Kitchen Renovations</li>
      <li>Bathroom Renovations</li>
      <li>House Renovations</li>
      <li>Garage Conversions</li>
      <li>Extensions</li>
      <li>Loft Conversions</li>
      <li>Conservatories</li>
      <li>Carpentry</li>
      <li>Tiling</li>
      <li>Electrical</li>
      <li>Plumbing &amp; Heating</li>
      <li>Bricklaying</li>
      <li>Landscaping</li>
      <li>Decorating</li>
      <li>Plastering</li>
    </ul>
    <div class="card__band"></div>
  </section>

  <section class="card card--front" aria-label="Card front – contact details">
    <div class="brand"><span class="brand__mark"></span>Varkelt Construction</div>
    <div class="person">
      <h1 class="person__name">Tomasz Brelwik</h1>
      <p class="person__title">Managing Director</p>
    </div>
    <div class="divider" aria-hidden="true"></div>
    <ul class="contact-phone">
      <li class="contact-item">
        <svg class="icon" viewBox="0 0 16 16" aria-hidden="true"><path d="M3 1l3 3-1.5 2c1 2 3 4 5 5L11.5 9.5l3 3L13 15C7 15 1 9 1 3z"/></svg>
        020 5194 6281
      </li>
      <li class="contact-item">
        <svg class="icon" viewBox="0 0 16 16" aria-hidden="true"><path d="M4 1h8v14H4z M5.5 3v9h5V3z" fill-rule="evenodd"/></svg>
        07845139072
      </li>
    </ul>
    <ul class="contact-online">
      <li class="contact-item">tomasz@varkelt.co.uk
        <svg class="icon" viewBox="0 0 16 16" aria-hidden="true"><path d="M1 3h14v10H1z M2 4l6 5 6-5" fill="none" stroke="#6cc03c" stroke-width="1.6"/></svg>
      </li>
      <li class="contact-item">www.varkelt.co.uk
        <svg class="icon" viewBox="0 0 16 16" aria-hidden="true"><g fill="none" stroke="#6cc03c" stroke-width="1.4"><circle cx="8" cy="8" r="6.5"/><ellipse cx="8" cy="8" rx="3" ry="6.5"/><path d="M1.5 8h13"/></g></svg>
      </li>
    </ul>
    <div class="card__band"></div>
  </section>

</body>
</html>
```